Norvane Website Design (New Start Up Investment Management Firm)

We need a website designed. We have attached a Powerpoint with our proposed website content (which is quite minimal), the format is just a suggestion but we would like to see your alternative and improved ideas. We are a boutique investment firm so are looking for something sleek and professional. I have included on the last page of the attachment our brand colours and font styles as well as attaching our logo design. We would like the successful designer to design the website and build the buttons etc.

On the "Contact Us" page, we are open to suggestions on how best to show the map, whether is should be static or open a google maps page. We would like the phone number and email address to be set up so people can click on them on their phone and it calls us or emails us directly.

We would prefer not to have photos of landscapes on the site.
Our website is hosted on a Linux based website.

We would also like 3 links at the bottom of each page for links to pdfs:
- Disclaimer, Terms and Conditions of Web Site Use
- Stewardship
- Pillar III

Target Market(s)

Institutional Investors

Industry/Entity Type

Investment

Coding

Coded - Design and coding required

Number of Pages Required

3 page

Font styles to use
Other font styles liked:
• Logo: Lato, Text: Source Sans Pro

Colors

Designer to choose colors to be used in the design.

Requirements
Must have
• The website must use the colours and fonts on the last page of the attached powerpoint. I can't see an option to select the exact colour palette below so please look at the PPT.
• For others please see Project description.
Should not have
• Landscape photos

```html
<!DOCTYPE html>
<html lang="en">
<head>
<meta charset="utf-8">
<title>Norvane Investment Management</title>
<link rel="stylesheet" href="https://fonts.googleapis.com/css2?family=Source+Sans+3:wght@300;400;600;700&display=swap">
<style>
:root{
  --navy:#0b2c5e;
  --ink:#1f2430;
  --text:#4a4f57;
  --muted:#5b6068;
  --accent:#5a9bd5;
  --button:#0a3ca0;
  --footer:#f5f5f5;
  --frame:#e6e6e6;
}
*{box-sizing:border-box;margin:0;padding:0}
html,body{width:1200px;height:969px;overflow:hidden;background:#fff;font-family:"Source Sans 3",sans-serif;color:var(--text)}
.page{position:relative;width:1200px;height:969px}
.brand{position:absolute;left:100px;top:40px;display:flex;align-items:center;gap:12px;color:var(--navy);font-size:40px;font-weight:600;letter-spacing:1px;text-decoration:none}
.brand-mark{width:50px;height:50px;background:var(--navy)}
.main-nav{position:absolute;top:50px;left:0;width:1200px;height:44px}
.main-nav a{position:absolute;font-size:20px;color:var(--muted);text-decoration:none;white-space:nowrap}
.main-nav a.active{color:var(--navy)}
.main-nav a.active::after{content:"";position:absolute;left:-6px;right:-9px;top:40px;height:3px;background:var(--accent)}
.hero{position:absolute;left:99px;top:127px;width:1002px;height:294px;border:1px solid var(--frame);background:#fff;padding:6px;box-shadow:0 14px 16px -12px rgba(0,0,0,.35)}
.hero-visual{width:100%;height:100%;background:linear-gradient(180deg,#dbe7f2 0%,#c9d6df 45%,#8aa07a 62%,#3f8fc0 78%,#2d7fb3 100%)}
.about-visual{position:absolute;left:246px;top:459px;width:183px;height:275px;background:linear-gradient(180deg,#3a7dc4 0%,#3a7dc4 55%,#2c3b4e 56%,#2c3b4e 100%);border-radius:6px}
.about{position:absolute;left:549px;top:538px;width:392px}
.about h2{font-size:28px;font-weight:300;color:var(--muted);margin-bottom:18px}
.about h2 strong{font-weight:700;color:var(--ink);margin-left:6px}
.about p{font-size:15px;line-height:22.3px;text-align:justify;margin-bottom:14px}
.btn{display:inline-block;height:24px;line-height:24px;padding:0 10px 0 14px;background:var(--button);color:#fff;font-size:12.5px;font-weight:600;text-decoration:none;border-left:4px solid var(--accent)}
.site-footer{position:absolute;left:0;top:806px;width:1200px;height:163px;background:var(--footer);text-align:center}
.footer-nav{margin-top:21px;display:flex;justify-content:center;gap:27px;font-size:15px}
.footer-nav a{color:var(--muted);text-decoration:none}
.footer-nav a.active{color:var(--navy)}
.social{display:flex;justify-content:center;gap:4px;margin-top:13px}
.social span{width:30px;height:30px;border-radius:50%;background:var(--button)}
.social span:nth-child(2){background:var(--accent)}
.social span:nth-child(3){background:var(--navy)}
.social span:nth-child(4){background:#6b7a8c}
.legal{margin-top:11px;font-size:11px;color:#111}
.legal a{color:#111;text-decoration:none}
.legal .sep{margin:0 6px}
.copyright{margin-top:8px;font-size:11px;color:#333}
</style>
</head>
<body>
<div class="page">
  <header>
    <a class="brand" href="#"><span class="brand-mark"></span>Norvane</a>
    <nav class="main-nav">
      <a class="active" href="#" style="left:461px">Home</a>
      <a href="#" style="left:546px">About Norvane</a>
      <a href="#" style="left:685px">Our Approach and Philosophy</a>
      <a href="#" style="left:980px">Contact Us</a>
    </nav>
  </header>

  <section class="hero">
    <div class="hero-visual" role="img" aria-label="Wide harbour city skyline banner"></div>
  </section>

  <section>
    <div class="about-visual" role="img" aria-label="Illustration of a potted plant growing a dollar coin"></div>
    <div class="about">
      <h2>About<strong>Norvane</strong></h2>
      <p>Norvane Investment Management was founded in 2016 with a clear vision to create an independent and nimble firm focused on generating superior risk-adjusted returns.</p>
      <a class="btn" href="#">Read More</a>
    </div>
  </section>

  <footer class="site-footer">
    <nav class="footer-nav">
      <a class="active" href="#">Home</a>
      <a href="#">About Norvane</a>
      <a href="#">Our Approach and Philosophy</a>
      <a href="#">Contact Us</a>
    </nav>
    <div class="social" aria-label="Social links"><span></span><span></span><span></span><span></span></div>
    <div class="legal"><a href="#">Disclaimer, Terms and Conditions</a><span class="sep">|</span><a href="#">Stewardship</a><span class="sep">|</span><a href="#">Pillar III</a></div>
    <div class="copyright">Copyrights © 2017, www.norvaneim.com. All Rights Reserved.</div>
  </footer>
</div>
</body>
</html>
```